Goodlooking website for a company who is working in the IT consultancy

We want a new website designed in WordPress. You can take www.vantoro.nl as an example. It should be a website with some short blocks of information about the company, nice pictures of our partners and our employees. A job page with a clear filter.

Target Market(s)

B2B

Industry/Entity Type

It Company

Coding

Coded - Design and coding required

Number of Pages Required

5+ page

Font styles to use
Sans Serif

Colors
0455a3
34a7d8

Requirements
Must have
• Check briefing

```html
<!DOCTYPE html>
<html lang="en">
<head>
<meta charset="utf-8">
<title>Kernova – Critical IT Systems</title>
<link href="https://fonts.googleapis.com/css2?family=Montserrat:wght@400;500;600&family=Open+Sans:wght@400;600&display=swap" rel="stylesheet">
<style>
:root{
  --blue:#1e9bd7;
  --blue-deep:#0455a3;
  --sky:#34a7d8;
  --teal:#1a9e8c;
  --navy:#0f2d3a;
  --ink:#1d2b33;
  --muted:#6b7780;
  --grey:#e4e4e4;
  --white:#ffffff;
}
*{margin:0;padding:0;box-sizing:border-box}
html,body{width:1200px;height:3879px;overflow:hidden;background:var(--white)}
body{position:relative;font-family:"Open Sans",sans-serif;color:var(--ink)}
.abs{position:absolute}
.bands{position:absolute;left:0;top:0;width:1200px;height:3879px}

/* header */
.brand{left:116px;top:24px;display:flex;align-items:center;gap:16px}
.brand-dot{width:66px;height:66px;border-radius:50%;background:var(--teal)}
.brand-name{font-family:"Montserrat",sans-serif;font-weight:500;font-size:38px;letter-spacing:3px;color:var(--navy);line-height:1}
.brand-tag{font-family:"Montserrat",sans-serif;font-size:10px;letter-spacing:2px;color:var(--teal);margin-top:5px}
.nav{top:44px;left:0;width:1200px}
.nav a{position:absolute;font-family:"Montserrat",sans-serif;font-size:16px;font-weight:500;color:var(--navy);text-decoration:none;white-space:nowrap}
.nav a.active{color:var(--blue)}
.nav-bar{left:540px;top:0;width:52px;height:5px;background:var(--blue)}

/* hero */
.hero-title{top:160px;width:1200px;text-align:center;font-family:"Montserrat",sans-serif;font-weight:500;line-height:1.15}
.hero-title .l1{font-size:42px;color:var(--blue);display:block}
.hero-title .l2{font-size:36px;color:var(--navy);display:block}
.hero-art{left:220px;top:285px;width:770px;height:362px;border-radius:8px;background:radial-gradient(ellipse at center,#dcebf3 0%,#eef5f9 55%,#ffffff 100%)}
.arrow-btn{width:52px;height:52px;border:3px solid var(--teal);border-radius:50%;top:328px}

/* section headings */
.sec-title{width:1200px;text-align:center;font-family:"Montserrat",sans-serif;font-weight:500;font-size:32px;letter-spacing:1px}
.divider{left:480px;width:240px;height:24px}

/* about */
.about-title{top:800px;color:var(--white)}
.about-text{top:892px;left:220px;width:760px;text-align:center;color:#e8f6f8;font-size:17px;line-height:1.6}
.about-text p+p{margin-top:14px}
.btn-outline{left:525px;top:1072px;width:168px;height:47px;border:2px solid var(--white);border-radius:24px;color:var(--white);font-family:"Montserrat",sans-serif;font-weight:600;font-size:16px;display:flex;align-items:center;justify-content:center}

/* services */
.services-title{top:1305px;color:var(--navy)}
.card{top:1448px;width:228px;height:267px;background:var(--white);box-shadow:0 4px 14px rgba(0,0,0,.16);text-align:center}
.card-icon{position:absolute;left:73px;top:-35px;width:82px;height:82px;border-radius:50%;background:var(--teal)}
.card h3{position:absolute;top:66px;left:10px;right:10px;font-family:"Montserrat",sans-serif;font-weight:500;font-size:19px;color:var(--blue);line-height:1.2}
.card p{position:absolute;top:118px;left:24px;right:24px;font-size:12.5px;color:var(--muted);line-height:1.5}
.card .more{position:absolute;top:208px;left:0;right:0;font-family:"Montserrat",sans-serif;font-weight:600;font-size:14px;color:var(--navy)}
.card .more::after{content:"";display:block;width:44px;height:2px;background:var(--blue);margin:6px auto 0}

/* contact */
.contact-title{top:1940px;color:var(--white)}
.field{height:44px;border:1.5px solid rgba(255,255,255,.75);color:#e6f4fb;font-size:13px;letter-spacing:.5px;padding:0 18px;display:flex;align-items:center}
.field.msg{align-items:flex-start;padding-top:12px}
.btn-dark{background:var(--navy);color:var(--white);border-radius:24px;font-family:"Montserrat",sans-serif;font-weight:600;font-size:17px;display:flex;align-items:center;justify-content:center}

/* partners */
.partners-title{top:2488px;color:var(--navy)}
.pill{top:2591px;width:230px;height:93px;border-radius:47px;background:var(--white);box-shadow:0 3px 12px rgba(0,0,0,.18);display:flex;align-items:center;justify-content:center}
.pill span{display:block;width:110px;height:40px;border-radius:6px;background:#c9d3da}

/* jobs */
.jobs-title{top:2838px;color:var(--navy)}
.job{left:189px;width:817px;height:92px;background:var(--white);border:1px solid #d7d7d7;box-shadow:0 2px 6px rgba(0,0,0,.08)}
.job-name{position:absolute;left:32px;top:24px;font-family:"Montserrat",sans-serif;font-size:20px;color:var(--navy)}
.job-co{position:absolute;left:32px;top:52px;font-size:12px;color:var(--blue)}
.job-meta{position:absolute;top:32px;font-size:14px;color:var(--blue);display:flex;align-items:center;gap:7px}
.job-desc{position:absolute;left:483px;top:30px;width:170px;font-size:12px;line-height:1.45;color:var(--ink)}
.job-btn{position:absolute;left:682px;top:30px;width:109px;height:34px;border:1.5px solid var(--blue);border-radius:17px;font-size:13px;color:var(--navy);display:flex;align-items:center;justify-content:center}

/* footer */
.foot-brand{left:130px;top:3548px;width:192px;text-align:center}
.foot-brand .brand-dot{margin:0 auto;width:70px;height:70px}
.foot-brand .brand-name{font-size:38px;margin-top:14px}
.social{top:3702px;left:170px;display:flex;gap:22px}
.social span{width:18px;height:18px;border-radius:50%;background:var(--blue-deep)}
.foot-col h4{font-family:"Montserrat",sans-serif;font-weight:600;font-size:19px;color:var(--navy);margin-bottom:16px}
.foot-col li{list-style:none;font-size:16px;color:var(--ink);line-height:31px}
.contact-line{display:flex;align-items:flex-start;gap:10px}
.rule{left:478px;top:3794px;width:608px;height:1px;background:#d5d5d5}
.copy{top:3815px;width:1200px;text-align:center;font-size:13px;color:var(--muted)}
</style>
</head>
<body>

<svg class="bands" viewBox="0 0 1200 3879" aria-hidden="true">
  <defs>
    <linearGradient id="aboutGrad" x1="0" x2="1" y1="0" y2="0">
      <stop offset="0" stop-color="#1a9e8c"/>
      <stop offset="1" stop-color="#1a8fc9"/>
    </linearGradient>
    <linearGradient id="contactGrad" x1="0" x2="1" y1="0" y2="1">
      <stop offset="0" stop-color="#2a8fd6"/>
      <stop offset="1" stop-color="#2f9fe0"/>
    </linearGradient>
  </defs>
  <polygon points="0,672 1200,690 1200,1120 0,1175" fill="url(#aboutGrad)"/>
  <polygon points="760,720 1200,705 1200,760" fill="var(--navy)"/>
  <polygon points="0,1165 0,1228 330,1205" fill="var(--navy)"/>
  <polygon points="0,1828 700,1852 0,1880" fill="var(--teal)"/>
  <polygon points="0,1866 560,1898 0,1935" fill="var(--navy)"/>
  <polygon points="0,1895 1200,1823 1200,2370 0,2444" fill="url(#contactGrad)"/>
  <polygon points="760,2382 1200,2345 1200,2412" fill="var(--navy)"/>
  <polygon points="0,2772 1200,2772 1200,3440 0,3470" fill="var(--grey)"/>
  <polygon points="680,2806 1200,2778 1200,2822" fill="var(--navy)"/>
  <polygon points="900,2805 1200,2795 1200,2806" fill="var(--blue-deep)"/>
  <polygon points="0,3440 420,3452 0,3495" fill="var(--blue)"/>
</svg>

<!-- header -->
<div class="abs brand">
  <div class="brand-dot"></div>
  <div>
    <div class="brand-name">KERNOVA</div>
    <div class="brand-tag">CRITICAL IT SYSTEMS</div>
  </div>
</div>
<div class="abs nav-bar"></div>
<nav class="abs nav">
  <a class="active" style="left:543px">HOME</a>
  <a style="left:632px">OUR SOLUTION</a>
  <a style="left:792px">OUR TEAM</a>
  <a style="left:916px">JOB</a>
  <a style="left:985px">CONTACT</a>
</nav>

<!-- hero -->
<h1 class="abs hero-title"><span class="l1">WE SHARE OUR KNOWLEDGE</span><span class="l2">WITH CUSTOMERS</span></h1>
<div class="abs hero-art" role="img" aria-label="Line illustration of a consultant working at a desk surrounded by charts, documents and team members"></div>
<svg class="abs arrow-btn" style="left:90px" viewBox="0 0 46 46"><polyline points="26,14 17,23 26,32" fill="none" stroke="#1a9e8c" stroke-width="3" stroke-linecap="round"/></svg>
<svg class="abs arrow-btn" style="left:1045px" viewBox="0 0 46 46"><polyline points="20,14 29,23 20,32" fill="none" stroke="#1a9e8c" stroke-width="3" stroke-linecap="round"/></svg>

<!-- about -->
<h2 class="abs sec-title about-title">ABOUT KERNOVA</h2>
<svg class="abs divider" style="top:842px" viewBox="0 0 240 24"><line x1="30" y1="12" x2="104" y2="12" stroke="#fff" stroke-width="2"/><line x1="136" y1="12" x2="210" y2="12" stroke="#fff" stroke-width="2"/><circle cx="120" cy="12" r="10" fill="none" stroke="#fff" stroke-width="2"/><line x1="110" y1="12" x2="130" y2="12" stroke="#fff" stroke-width="1.5"/><ellipse cx="120" cy="12" rx="4" ry="10" fill="none" stroke="#fff" stroke-width="1.5"/></svg>
<div class="abs about-text">
  <p>Praesent elementum elit at tellus nec ultricies sit amet porttitor mattis enim In massa libero interdum nec interdum vel blandit sed nulla In ullamcorper</p>
  <p>est eget tempor cursus neque mi consectetuer mi a ultricies massa est sed nisl Class aptent taciti sociosqu ad litora torquent per conubia nostra per inceptos hymenaeos Proin nulla arcu nonummy luctus dictum eget fermentum et lorem</p>
</div>
<div class="abs btn-outline">Learn More</div>

<!-- services -->
<h2 class="abs sec-title services-title">WHAT WE DO</h2>
<svg class="abs divider" style="top:1350px" viewBox="0 0 240 24"><line x1="30" y1="12" x2="104" y2="12" stroke="#1e9bd7" stroke-width="2"/><line x1="136" y1="12" x2="210" y2="12" stroke="#1e9bd7" stroke-width="2"/><circle cx="120" cy="12" r="11" fill="#1e9bd7"/><line x1="110" y1="12" x2="130" y2="12" stroke="#fff" stroke-width="1.5"/><ellipse cx="120" cy="12" rx="4" ry="10" fill="none" stroke="#fff" stroke-width="1.5"/></svg>

<div class="abs card" style="left:116px"><div class="card-icon"></div><h3>Automation &amp;<br>Deployment</h3><p>Class aptent taciti sociosqu ad litora torquent per conubia nostra per inceptos hymenaeos Proin</p><div class="more">READ MORE</div></div>
<div class="abs card" style="left:367px"><div class="card-icon"></div><h3>Mission Critical<br>Solutions</h3><p>Class aptent taciti sociosqu ad litora torquent per conubia nostra per inceptos hymenaeos Proin</p><div class="more">READ MORE</div></div>
<div class="abs card" style="left:618px"><div class="card-icon"></div><h3>Cloud<br>Consultancy</h3><p>Class aptent taciti sociosqu ad litora torquent per conubia nostra per inceptos hymenaeos Proin</p><div class="more">READ MORE</div></div>
<div class="abs card" style="left:869px"><div class="card-icon"></div><h3>Hyperconverged<br>Infrastructures</h3><p>Class aptent taciti sociosqu ad litora torquent per conubia nostra per inceptos hymenaeos Proin</p><div class="more">READ MORE</div></div>

<!-- contact -->
<h2 class="abs sec-title contact-title">CONTACT US FORM</h2>
<svg class="abs divider" style="top:1985px" viewBox="0 0 240 24"><line x1="30" y1="12" x2="104" y2="12" stroke="#fff" stroke-width="2"/><line x1="136" y1="12" x2="210" y2="12" stroke="#fff" stroke-width="2"/><circle cx="120" cy="12" r="10" fill="none" stroke="#fff" stroke-width="2"/><line x1="110" y1="12" x2="130" y2="12" stroke="#fff" stroke-width="1.5"/><ellipse cx="120" cy="12" rx="4" ry="10" fill="none" stroke="#fff" stroke-width="1.5"/></svg>
<div class="abs field" style="left:212px;top:2038px;width:380px">FIRST NAME</div>
<div class="abs field" style="left:600px;top:2038px;width:383px">LAST NAME</div>
<div class="abs field" style="left:212px;top:2095px;width:380px">EMAIL ADDRESS</div>
<div class="abs field" style="left:600px;top:2095px;width:383px">PHONE</div>
<div class="abs field msg" style="left:212px;top:2152px;width:771px;height:82px">MESSAGE</div>
<div class="abs btn-dark" style="left:517px;top:2255px;width:192px;height:47px">SUBMIT</div>

<!-- partners -->
<h2 class="abs sec-title partners-title">OUR PARTNERS</h2>
<svg class="abs divider" style="top:2534px" viewBox="0 0 240 24"><line x1="30" y1="12" x2="104" y2="12" stroke="#1e9bd7" stroke-width="2"/><line x1="136" y1="12" x2="210" y2="12" stroke="#1e9bd7" stroke-width="2"/><circle cx="120" cy="12" r="11" fill="#1e9bd7"/><line x1="110" y1="12" x2="130" y2="12" stroke="#fff" stroke-width="1.5"/><ellipse cx="120" cy="12" rx="4" ry="10" fill="none" stroke="#fff" stroke-width="1.5"/></svg>
<div class="abs pill" style="left:119px"><span></span></div>
<div class="abs pill" style="left:362px"><span></span></div>
<div class="abs pill" style="left:608px"><span></span></div>
<div class="abs pill" style="left:851px"><span></span></div>

<!-- jobs -->
<h2 class="abs sec-title jobs-title">JOB LISTINGS</h2>
<svg class="abs divider" style="top:2884px" viewBox="0 0 240 24"><line x1="30" y1="12" x2="104" y2="12" stroke="#1e9bd7" stroke-width="2"/><line x1="136" y1="12" x2="210" y2="12" stroke="#1e9bd7" stroke-width="2"/><circle cx="120" cy="12" r="11" fill="#1e9bd7"/><line x1="110" y1="12" x2="130" y2="12" stroke="#fff" stroke-width="1.5"/><ellipse cx="120" cy="12" rx="4" ry="10" fill="none" stroke="#fff" stroke-width="1.5"/></svg>

<div class="abs job" style="top:2935px">
  <div class="job-name">Job Title here</div><div class="job-co">Company Name</div>
  <div class="job-meta" style="left:198px"><svg width="14" height="14" viewBox="0 0 14 14"><circle cx="7" cy="7" r="6" fill="none" stroke="#1e9bd7" stroke-width="1.5"/><polyline points="7,3.5 7,7 9.5,8.5" fill="none" stroke="#1e9bd7" stroke-width="1.5"/></svg>Full Time</div>
  <div class="job-meta" style="left:335px"><svg width="12" height="16" viewBox="0 0 12 16"><path d="M6 15C2 10 1 8 1 6a5 5 0 0 1 10 0c0 2-1 4-5 9z" fill="#1e9bd7"/><circle cx="6" cy="6" r="2" fill="#fff"/></svg>Location City</div>
  <div class="job-desc">Ut nisi erat fermentum vel congue id euismo</div>
  <div class="job-btn">View Details</div>
</div>
<div class="abs job" style="top:3032px">
  <div class="job-name">Job Title here</div><div class="job-co">Company Name</div>
  <div class="job-meta" style="left:198px"><svg width="14" height="14" viewBox="0 0 14 14"><circle cx="7" cy="7" r="6" fill="none" stroke="#1e9bd7" stroke-width="1.5"/><polyline points="7,3.5 7,7 9.5,8.5" fill="none" stroke="#1e9bd7" stroke-width="1.5"/></svg>Full Time</div>
  <div class="job-meta" style="left:335px"><svg width="12" height="16" viewBox="0 0 12 16"><path d="M6 15C2 10 1 8 1 6a5 5 0 0 1 10 0c0 2-1 4-5 9z" fill="#1e9bd7"/><circle cx="6" cy="6" r="2" fill="#fff"/></svg>Location City</div>
  <div class="job-desc">Ut nisi erat fermentum vel congue id euismo</div>
  <div class="job-btn">View Details</div>
</div>
<div class="abs job" style="top:3128px">
  <div class="job-name">Job Title here</div><div class="job-co">Company Name</div>
  <div class="job-meta" style="left:198px"><svg width="14" height="14" viewBox="0 0 14 14"><circle cx="7" cy="7" r="6" fill="none" stroke="#1e9bd7" stroke-width="1.5"/><polyline points="7,3.5 7,7 9.5,8.5" fill="none" stroke="#1e9bd7" stroke-width="1.5"/></svg>Full Time</div>
  <div class="job-meta" style="left:335px"><svg width="12" height="16" viewBox="0 0 12 16"><path d="M6 15C2 10 1 8 1 6a5 5 0 0 1 10 0c0 2-1 4-5 9z" fill="#1e9bd7"/><circle cx="6" cy="6" r="2" fill="#fff"/></svg>Location City</div>
  <div class="job-desc">Ut nisi erat fermentum vel congue id euismo</div>
  <div class="job-btn">View Details</div>
</div>
<div class="abs job" style="top:3224px">
  <div class="job-name">Job Title here</div><div class="job-co">Company Name</div>
  <div class="job-meta" style="left:198px"><svg width="14" height="14" viewBox="0 0 14 14"><circle cx="7" cy="7" r="6" fill="none" stroke="#1e9bd7" stroke-width="1.5"/><polyline points="7,3.5 7,7 9.5,8.5" fill="none" stroke="#1e9bd7" stroke-width="1.5"/></svg>Full Time</div>
  <div class="job-meta" style="left:335px"><svg width="12" height="16" viewBox="0 0 12 16"><path d="M6 15C2 10 1 8 1 6a5 5 0 0 1 10 0c0 2-1 4-5 9z" fill="#1e9bd7"/><circle cx="6" cy="6" r="2" fill="#fff"/></svg>Location City</div>
  <div class="job-desc">Ut nisi erat fermentum vel congue id euismo</div>
  <div class="job-btn">View Details</div>
</div>
<div class="abs btn-dark" style="left:517px;top:3346px;width:181px;height:44px">VIEW ALL</div>

<!-- footer -->
<div class="abs foot-brand">
  <div class="brand-dot"></div>
  <div class="brand-name">KERNOVA</div>
  <div class="brand-tag">CRITICAL IT SYSTEMS</div>
</div>
<div class="abs social"><span></span><span></span><span></span></div>

<div class="abs foot-col" style="left:409px;top:3553px">
  <h4>COMPANY</h4>
  <ul><li>Home</li><li>About Us</li><li>Solutions</li><li>Out Team</li></ul>
</div>
<div class="abs foot-col" style="left:618px;top:3553px">
  <h4>RESOURCES</h4>
  <ul><li>Partners</li><li>job</li><li>Contact</li></ul>
</div>
<div class="abs foot-col" style="left:820px;top:3553px">
  <h4>CONTACT US</h4>
  <ul>
    <li class="contact-line"><svg width="14" height="31" viewBox="0 0 14 31"><path d="M7 23C3 18 2 16 2 14a5 5 0 0 1 10 0c0 2-1 4-5 9z" fill="#1e9bd7"/><circle cx="7" cy="14" r="2" fill="#fff"/></svg>Keplerstraat 14, 3531<br>KV Utrecht</li>
    <li class="contact-line"><svg width="14" height="31" viewBox="0 0 14 31"><path d="M3 9c1-1 3-1 3 1l1 3c0 1-1 2-1 2 1 2 2 3 4 4 0 0 1-1 2-1l2 1c1 1 1 2 0 3-3 3-12-6-11-13z" fill="#1e9bd7"/></svg>085-7316402</li>
    <li class="contact-line"><svg width="14" height="31" viewBox="0 0 14 31"><rect x="1" y="10" width="13" height="10" rx="1" fill="#1e9bd7"/><polyline points="1,11 7.5,16 14,11" fill="none" stroke="#fff" stroke-width="1.3"/></svg>info@kernova.nl</li>
  </ul>
</div>
<div class="abs rule"></div>
<div class="abs copy">© 2018 Company Name &nbsp;All right reserved</div>

</body>
</html>
```